Field Trip Flyer

We need a flyer to promote our field trips. I would like the flyer to be bright, eye popping and modern. We offer STEM Field Trips as well for an educational opportunity that connects roller skating and STEM concepts. We offer field trips for 2 or 3 hours and all field trips include skating, skate rental, play zone, arcade games available, concessions available, + much more! Field trips are fun, unique and engaging and can be booked online at brindlewayrink.com. Our business name is Brindleway Skate Center. The flyer design needs to be front and back.

Target Market(s)

Elementary School Teachers

Requirements
Must have
• Front and Back Design, 5.5 x 8.5,Field Trip Inclusions: Skating, skate rental, play zone, arcade available, concessions available + much more!, STEM Field Trips available, book online at brindlewayrink.com
Nice to have
• engaging key words to describe the field trips
Should not have
• too much words or irrelevant information

```html
<!DOCTYPE html>
<html lang="en">
<head>
<meta charset="utf-8">
<title>Brindleway Skate Center – STEM Field Trips Flyer</title>
<link href="https://fonts.googleapis.com/css2?family=Fredoka:wght@600;700&family=Roboto+Condensed:wght@500;700&family=Source+Sans+3:wght@600&display=swap" rel="stylesheet">
<style>
  :root{
    --page:#dcdddf;
    --navy:#23337f;
    --royal:#2f43a3;
    --sky:#27aee8;
    --red:#e3202e;
    --yellow:#f7d117;
    --lime:#c3d82e;
    --tag-blue:#1f63b8;
    --paper:#f2f3f7;
    --white:#ffffff;
    --ink-blue:#2d3f9c;
    --glow:#d7f03a;
  }
  *{box-sizing:border-box;margin:0;padding:0}
  html,body{width:1200px;height:946px;overflow:hidden;background:var(--page)}
  .sheet{position:relative;width:1200px;height:946px}
  .flyer{position:absolute;top:93px;width:490px;height:760px;overflow:hidden;box-shadow:0 6px 18px rgba(0,0,0,.28)}
  .flyer--front{left:75px;background:linear-gradient(160deg,var(--royal),var(--navy))}
  .flyer--back{left:635px;background:var(--paper)}
  .flyer svg.shapes{position:absolute;inset:0;width:490px;height:760px}

  .badge{position:absolute;border-radius:50%;background:var(--white);display:flex;align-items:center;justify-content:center;
    font-family:"Fredoka",sans-serif;font-weight:700;color:var(--navy);text-align:center;line-height:1;box-shadow:0 2px 6px rgba(0,0,0,.3)}
  .badge--front{left:2px;top:193px;width:160px;height:160px;font-size:25px}
  .badge--back{left:10px;top:92px;width:128px;height:128px;font-size:20px}

  .tag{position:absolute;font-family:"Fredoka",sans-serif;font-weight:600;letter-spacing:1px;display:flex;align-items:center;justify-content:center}
  .tag span{display:inline-block}
  .tag--skating{left:355px;top:90px;width:130px;height:58px;background:var(--yellow);color:var(--tag-blue);font-size:24px;transform:rotate(-4deg) skewX(-6deg)}
  .tag--playzone{left:340px;top:162px;width:168px;height:62px;background:var(--lime);color:var(--white);font-size:24px;transform:rotate(3deg) skewX(-8deg)}
  .tag--arcade{left:300px;top:248px;width:180px;height:58px;background:var(--tag-blue);color:var(--white);font-size:24px;transform:rotate(9deg) skewX(-12deg)}

  .title-stem{position:absolute;font-family:"Fredoka",sans-serif;font-weight:700;color:var(--white);letter-spacing:2px;line-height:1;
    text-shadow:0 0 4px var(--glow),0 0 10px var(--glow),0 0 2px var(--glow)}
  .title-trips{position:absolute;font-family:"Fredoka",sans-serif;font-weight:700;line-height:1;
    background:linear-gradient(#f4f4f4,#9c9ea3 55%,#d8d9dc);-webkit-background-clip:text;background-clip:text;color:transparent;
    filter:drop-shadow(2px 3px 0 rgba(0,0,0,.45))}
  .flyer--front .title-stem{left:0;width:470px;top:352px;text-align:center;font-size:108px}
  .flyer--front .title-trips{left:0;width:470px;top:470px;text-align:center;font-size:50px}
  .flyer--back .title-stem{left:135px;top:12px;font-size:98px}
  .flyer--back .title-trips{left:145px;top:104px;font-size:46px}

  .lead{position:absolute;left:20px;width:450px;top:528px;text-align:center;font-family:"Source Sans 3",sans-serif;font-weight:600;
    color:var(--white);font-size:15px;line-height:1.3}
  .lead a{color:var(--glow);text-decoration:none}

  .contact{position:absolute;right:20px;top:684px;text-align:right;font-family:"Roboto Condensed",sans-serif;font-style:normal;line-height:1}
  .contact__name{font-weight:700;font-size:16px;height:18px;margin-bottom:3px}
  .contact__line{display:flex;justify-content:flex-end;align-items:center;gap:6px;height:12px;font-size:10px;font-weight:500;margin-top:2px}
  .contact__line svg{width:12px;height:12px;flex:none}
  .flyer--front .contact{color:var(--ink-blue)}
  .flyer--front .contact__line{color:#444}
  .flyer--back .contact{color:var(--white)}

  .offer{position:absolute;left:10px;width:260px;top:458px;text-align:center;font-family:"Roboto Condensed",sans-serif;font-weight:700;
    color:var(--red);font-size:19px;line-height:1.25}
  .inclusions-head{position:absolute;left:12px;top:545px;width:245px;height:42px;background:var(--lime);display:flex;align-items:center;
    padding-left:14px;font-family:"Roboto Condensed",sans-serif;font-weight:700;font-size:18px;color:var(--ink-blue);transform:skewY(-1.5deg)}
  .inclusions{position:absolute;left:16px;top:618px;list-style:none;font-family:"Roboto Condensed",sans-serif;font-weight:700;
    font-size:15.5px;color:var(--ink-blue);line-height:18px}
  .inclusions li{display:flex;align-items:center;gap:8px}
  .inclusions li::before{content:"›";display:inline-flex;align-items:center;justify-content:center;width:12px;height:12px;border-radius:50%;
    background:var(--lime);color:var(--white);font-size:12px;line-height:1}
</style>
</head>
<body>
<main class="sheet">

  <section class="flyer flyer--front" aria-label="Flyer front">
    <svg class="shapes" viewBox="0 0 490 760">
      <path d="M0,0 H352 C392,130 342,282 205,328 C125,352 45,338 0,312 Z" fill="var(--red)"/>
      <path role="img" aria-label="Photo: children smiling at an arcade game with a teacher" d="M0,0 H340 C378,126 330,270 200,316 C122,340 44,326 0,300 Z" fill="url(#warmPhoto)"/>
      <path d="M0,760 H490 V600 C440,640 380,660 300,668 C230,676 200,720 170,760 Z" fill="var(--sky)"/>
      <path d="M0,760 H490 V620 C440,655 380,672 310,680 C245,688 215,730 190,760 Z" fill="var(--paper)"/>
      <circle cx="208" cy="636" r="57" fill="var(--white)"/>
      <circle role="img" aria-label="Photo: smiling young boy" cx="208" cy="636" r="52" fill="url(#bluePhoto)"/>
      <circle cx="92" cy="654" r="90" fill="var(--white)"/>
      <circle role="img" aria-label="Photo: girls building a STEM project together" cx="92" cy="654" r="84" fill="url(#tablePhoto)"/>
      <defs>
        <linearGradient id="warmPhoto" x1="0" y1="0" x2="1" y2="1"><stop offset="0" stop-color="#3a2419"/><stop offset=".5" stop-color="#8a7fa8"/><stop offset="1" stop-color="#5a6fa8"/></linearGradient>
        <linearGradient id="bluePhoto" x1="0" y1="0" x2="1" y2="1"><stop offset="0" stop-color="#6c4a3a"/><stop offset="1" stop-color="#4e79b8"/></linearGradient>
        <linearGradient id="tablePhoto" x1="0" y1="0" x2="1" y2="1"><stop offset="0" stop-color="#c9b8a6"/><stop offset="1" stop-color="#5b5a6e"/></linearGradient>
      </defs>
    </svg>

    <div class="tag tag--skating"><span>SKATING</span></div>
    <div class="tag tag--playzone"><span>PLAY ZONE</span></div>
    <div class="tag tag--arcade"><span>ARCADE</span></div>

    <div class="badge badge--front">Brindleway<br>Skate</div>

    <h1 class="title-stem">STEM</h1>
    <h2 class="title-trips">FIELD TRIPS</h2>
    <p class="lead">Field trips are fun, unique and engaging and can be booked<br>online at <a href="#">brindlewayrink.com</a></p>

    <address class="contact">
      <div class="contact__name">BRINDLEWAY SKATE CENTER</div>
      <div class="contact__line">555-014-2290 <svg viewBox="0 0 12 12"><circle cx="6" cy="6" r="6" fill="var(--ink-blue)"/><path d="M4 3l1 .2.5 1.5-.7.6a4 4 0 0 0 1.9 1.9l.6-.7 1.5.5L9 8a1.3 1.3 0 0 1-1.5.9A5 5 0 0 1 3.1 4.5 1.3 1.3 0 0 1 4 3z" fill="#fff"/></svg></div>
      <div class="contact__line">www.brindlewayrink.com <svg viewBox="0 0 12 12"><circle cx="6" cy="6" r="6" fill="var(--ink-blue)"/><circle cx="6" cy="6" r="3.3" fill="none" stroke="#fff" stroke-width=".9"/><path d="M2.7 6h6.6M6 2.7v6.6" stroke="#fff" stroke-width=".8"/></svg></div>
      <div class="contact__line">48 Linden Avenue <svg viewBox="0 0 12 12"><circle cx="6" cy="6" r="6" fill="var(--ink-blue)"/><path d="M6 2.8l3 2.6H8.2V9H3.8V5.4H3z" fill="#fff"/></svg></div>
    </address>
  </section>

  <section class="flyer flyer--back" aria-label="Flyer back">
    <svg class="shapes" viewBox="0 0 490 760">
      <path d="M0,0 H490 V170 C330,205 160,170 0,210 Z" fill="var(--navy)"/>
      <path d="M0,232 C20,330 40,400 95,430 L60,440 C15,400 0,330 0,290 Z" fill="var(--sky)"/>
      <path d="M40,200 C180,170 330,198 490,152 V165 C330,212 180,186 40,214 Z" fill="var(--red)"/>
      <path role="img" aria-label="Photo: smiling girl roller skating at the rink with classmates" d="M40,212 C180,184 330,210 490,165 V410 C380,438 230,438 110,426 C70,400 45,330 40,212 Z" fill="url(#rinkPhoto)"/>
      <path d="M210,760 C250,700 310,680 380,676 C430,672 470,655 490,630 V760 Z" fill="var(--royal)"/>
      <circle cx="397" cy="427" r="95" fill="var(--white)"/>
      <circle role="img" aria-label="Photo: group of students cheering at the rink" cx="397" cy="427" r="89" fill="url(#groupPhoto)"/>
      <circle cx="307" cy="530" r="77" fill="var(--white)"/>
      <circle role="img" aria-label="Photo: three girls smiling in the play zone" cx="307" cy="530" r="71" fill="url(#playPhoto)"/>
      <circle cx="419" cy="573" r="62" fill="var(--white)"/>
      <circle role="img" aria-label="Photo: boy with glasses smiling" cx="419" cy="573" r="56" fill="url(#boyPhoto)"/>
      <defs>
        <linearGradient id="rinkPhoto" x1="0" y1="0" x2="1" y2="1"><stop offset="0" stop-color="#6c9fd0"/><stop offset=".5" stop-color="#c9c4e6"/><stop offset="1" stop-color="#d98fc8"/></linearGradient>
        <linearGradient id="groupPhoto" x1="0" y1="0" x2="1" y2="1"><stop offset="0" stop-color="#7a4b3a"/><stop offset="1" stop-color="#c8b7c4"/></linearGradient>
        <linearGradient id="playPhoto" x1="0" y1="0" x2="1" y2="1"><stop offset="0" stop-color="#3a3f6e"/><stop offset="1" stop-color="#2a6cc0"/></linearGradient>
        <linearGradient id="boyPhoto" x1="0" y1="0" x2="1" y2="1"><stop offset="0" stop-color="#a88a80"/><stop offset="1" stop-color="#58a3c8"/></linearGradient>
      </defs>
    </svg>

    <div class="badge badge--back">Brindleway<br>Skate</div>
    <h1 class="title-stem">STEM</h1>
    <h2 class="title-trips">FIELD TRIPS</h2>

    <p class="offer">WE OFFER FIELD TRIPS<br>FOR 2 OR 3 HOURS<br>AND ALL FIELD TRIPS</p>
    <div class="inclusions-head">FIELD TRIP INCLUSIONS:</div>
    <ul class="inclusions">
      <li>SKATING</li>
      <li>SKATE RENTAL</li>
      <li>PLAY ZONE</li>
      <li>ARCADE GAMES AVAILABLE</li>
      <li>CONCESSIONS AVAILABLE</li>
      <li>+ MUCH MORE!</li>
    </ul>

    <address class="contact">
      <div class="contact__name">BRINDLEWAY SKATE CENTER</div>
      <div class="contact__line">555-014-2290 <svg viewBox="0 0 12 12"><circle cx="6" cy="6" r="6" fill="var(--lime)"/><path d="M4 3l1 .2.5 1.5-.7.6a4 4 0 0 0 1.9 1.9l.6-.7 1.5.5L9 8a1.3 1.3 0 0 1-1.5.9A5 5 0 0 1 3.1 4.5 1.3 1.3 0 0 1 4 3z" fill="var(--navy)"/></svg></div>
      <div class="contact__line">www.brindlewayrink.com <svg viewBox="0 0 12 12"><circle cx="6" cy="6" r="6" fill="var(--lime)"/><circle cx="6" cy="6" r="3.3" fill="none" stroke="var(--navy)" stroke-width=".9"/><path d="M2.7 6h6.6M6 2.7v6.6" stroke="var(--navy)" stroke-width=".8"/></svg></div>
      <div class="contact__line">48 Linden Avenue <svg viewBox="0 0 12 12"><circle cx="6" cy="6" r="6" fill="var(--lime)"/><path d="M6 2.8l3 2.6H8.2V9H3.8V5.4H3z" fill="var(--navy)"/></svg></div>
    </address>
  </section>

</main>
</body>
</html>
```